Card Design for my dog training business Brightpaw Obedience

Need a business card design for my dog training business with my new logo. Want the card to come off professional yet fun. Want it to be very eye catchy as well. I normally have these at vet clinics, pet stores, and groomers. so need it to look better than my competitors.
Target Market(s)
dog owners
Industry/Entity Type
Dog Training
Contact Information for Business Card
needs logo, my name and info
Font styles to use
Serif
Colors
0255a3
ffffff
ec1f27
000000
333333
fbfbfb
Requirements
Must have
- Brightpaw Obedience
- Felix Orland
- 415 903 2276
- info@brightpawobedience.example
- www.brightpawobedience.example

```html
<!DOCTYPE html>
<html lang="en">
<head>
<meta charset="utf-8">
<title>Brightpaw Obedience – Business Card</title>
<link href="https://fonts.googleapis.com/css2?family=Cinzel:wght@500&family=Open+Sans:wght@400&display=swap" rel="stylesheet">
<style>
  :root {
    --backdrop: #8c8c8c;
    --card-white: #ffffff;
    --card-black: #000000;
    --ink: #111111;
    --ink-soft: #333333;
    --brand-blue: #0255a3;
    --brand-red: #ec1f27;
    --art-grey: #a9a9a9;
    --art-mid: #6e6e6e;
  }
  html, body {
    margin: 0;
    width: 1200px;
    height: 1200px;
    overflow: hidden;
    background: var(--backdrop);
  }
  .canvas {
    position: relative;
    width: 1200px;
    height: 1200px;
  }
  .card {
    position: absolute;
    top: 310px;
    height: 594px;
    box-shadow: 0 3px 6px rgba(0,0,0,0.35);
  }
  .card-front {
    left: 234px;
    width: 364px;
    background: var(--card-white);
  }
  .card-back {
    left: 627px;
    width: 368px;
    background: var(--card-black);
    overflow: hidden;
  }
  .logo-art {
    position: absolute;
    left: 48px;
    top: 85px;
    width: 266px;
    height: 190px;
    border-radius: 6px;
    background: linear-gradient(160deg, #e6e6e6 0%, #cfd6df 55%, #f2f2f2 100%);
  }
  .wordmark {
    position: absolute;
    left: 0;
    right: 0;
    top: 292px;
    text-align: center;
    font-family: "Cinzel", serif;
    font-weight: 500;
    font-size: 21px;
    letter-spacing: 1px;
    color: var(--ink);
  }
  .wordmark-rule {
    position: absolute;
    left: 116px;
    width: 134px;
    height: 2px;
    top: 338px;
    background: var(--brand-blue);
  }
  .person-name {
    position: absolute;
    left: 0;
    right: 0;
    top: 400px;
    text-align: center;
    font-family: "Cinzel", serif;
    font-weight: 500;
    font-size: 27px;
    letter-spacing: 1px;
    color: var(--ink);
    margin: 0;
  }
  .icon-row {
    position: absolute;
    left: 87px;
    top: 449px;
  }
  .contact-list {
    position: absolute;
    left: 0;
    right: 0;
    top: 485px;
    margin: 0;
    padding: 0;
    list-style: none;
    text-align: center;
    font-family: "Open Sans", sans-serif;
    font-size: 15.5px;
    line-height: 21.5px;
    color: var(--ink-soft);
  }
  .back-art {
    position: absolute;
    left: 0;
    top: 115px;
    width: 368px;
    height: 425px;
    background:
      linear-gradient(200deg, rgba(2,85,163,0.18) 0%, rgba(0,0,0,0) 45%),
      linear-gradient(20deg, rgba(236,31,39,0.14) 0%, rgba(0,0,0,0) 40%),
      linear-gradient(180deg, var(--art-grey) 0%, var(--art-mid) 48%, var(--art-grey) 100%);
  }
</style>
</head>
<body>
<main class="canvas">
  <section class="card card-front" aria-label="Business card front">
    <div class="logo-art" role="img" aria-label="Illustration of two dog heads inside a state outline"></div>
    <div class="wordmark">Brightpaw Obedience</div>
    <div class="wordmark-rule"></div>
    <h1 class="person-name">Felix Orland</h1>
    <svg class="icon-row" width="190" height="24" viewBox="0 0 190 24" aria-hidden="true">
      <line x1="0" y1="12" x2="50" y2="12" stroke="#111" stroke-width="1.3"/>
      <line x1="140" y1="12" x2="190" y2="12" stroke="#111" stroke-width="1.3"/>
      <circle cx="72" cy="12" r="10" fill="#0255a3"/>
      <circle cx="95" cy="12" r="10" fill="#ec1f27"/>
      <circle cx="118" cy="12" r="10" fill="#0255a3"/>
      <path d="M67 9 q5 -4 10 0 l-1.5 2 h-2 l-0.5 -1 h-2 l-0.5 1 h-2 z M68 13 h8 v3 h-8 z" fill="#fff"/>
      <rect x="89" y="8" width="12" height="8" fill="none" stroke="#fff" stroke-width="1.3"/>
      <path d="M89 8 l6 5 l6 -5" fill="none" stroke="#fff" stroke-width="1.3"/>
      <circle cx="118" cy="12" r="5.5" fill="none" stroke="#fff" stroke-width="1.3"/>
      <ellipse cx="118" cy="12" rx="2.3" ry="5.5" fill="none" stroke="#fff" stroke-width="1"/>
      <line x1="112.5" y1="12" x2="123.5" y2="12" stroke="#fff" stroke-width="1"/>
    </svg>
    <ul class="contact-list">
      <li>415 903 2276</li>
      <li>info@brightpawobedience.example</li>
      <li>www.brightpawobedience.example</li>
    </ul>
  </section>
  <section class="card card-back" aria-label="Business card back">
    <div class="back-art" role="img" aria-label="Large grey illustration of two dog heads on black"></div>
  </section>
</main>
</body>
</html>
```